Tech Savy small Business accountant business card design

We need a business card for a new company based in the cloud. We provide tax, business advisory, accounting, information technology solutions and back office functions to small businesses. We offer fixed fee packages with add on services as you need them. By harnessing technology we simplify small business operational processes providing valuable time and information for small business owners to grow their business. In the logo (bluvoria) we want to be able to see bluv and experts. The final design should communicate achieving growth dreams and balance (ie life and $).
Updates
This project has been temporarily placed on hold until I finalize "Tech Savy small Business accountant needs a logo". I invite all designers to submit on this logo project. Once my logo is finalized I will resume this business card contest. Thanks Added Wednesday, March 19, 2014
This project has been temporarily placed on hold until I finalize "Tech Savy small Business accountant logo". I invite all designers to submit on this logo project. Once my logo is finalized I will resume this business card contest. Thanks Added Thursday, March 20, 2014
Target Market(s)
Small Business (Revenue $500,000, more than 3 employees) owners.
Industry/Entity Type
Small Business
Contact Information for Business Card
Marcy Elwind (Principal)
Accountant, Tax Agent.
TEL | 0417 683 912
EMAIL | Marcy.Elwind@bluvoria.com.au
WEB | www.bluvoria.com.au
Look and feel

```html
<!DOCTYPE html>
<html lang="en">
<head>
<meta charset="utf-8">
<title>Bluvoria business card</title>
<link href="https://fonts.googleapis.com/css2?family=Questrial&display=swap" rel="stylesheet">
<style>
  :root {
    --page-bg: #e9e6e1;
    --card-white: #f7f7f7;
    --card-white-edge: #e4e4e4;
    --card-grey-light: #8d8d92;
    --card-grey-dark: #5b5b60;
    --brand-blue: #21a9dc;
    --text-grey: #6e6e6e;
    --text-soft: #d9d9dc;
  }
  * { box-sizing: border-box; margin: 0; padding: 0; }
  html, body { width: 1200px; height: 780px; overflow: hidden; }
  body {
    background: var(--page-bg);
    font-family: "Questrial", "Century Gothic", sans-serif;
    position: relative;
  }
  .card {
    position: absolute;
    width: 540px;
    height: 330px;
    border-radius: 3px;
    box-shadow: 0 10px 24px rgba(0,0,0,0.18);
  }
  /* Front */
  .card-front {
    left: 40px; top: 225px;
    background: linear-gradient(135deg, #ffffff 0%, var(--card-white) 55%, var(--card-white-edge) 100%);
  }
  .front-brand {
    position: absolute; left: 34px; top: 40px;
  }
  .brand-name {
    color: var(--brand-blue);
    font-size: 54px;
    line-height: 1;
    letter-spacing: -1px;
  }
  .front-brand .tagline {
    color: var(--text-grey);
    font-size: 15px;
    margin-top: 8px;
    letter-spacing: 0.3px;
  }
  .person {
    position: absolute; right: 30px; top: 50px;
    text-align: right;
  }
  .person-name {
    color: var(--brand-blue);
    font-size: 25px;
    line-height: 1.1;
  }
  .divider {
    position: absolute;
    left: 150px; right: 30px; top: 88px;
    height: 1.5px;
    background: var(--brand-blue);
  }
  .person-role {
    position: absolute; right: 30px; top: 96px;
    text-align: right;
    color: var(--text-grey);
    font-size: 13px;
    line-height: 1.35;
  }
  .address {
    position: absolute; right: 30px; top: 158px;
    text-align: right;
    color: var(--text-grey);
    font-size: 13px;
    line-height: 1.35;
  }
  .contact-list {
    position: absolute; left: 34px; bottom: 34px;
    list-style: none;
  }
  .contact-item {
    display: flex; align-items: center; gap: 9px;
    color: var(--text-grey);
    font-size: 14px;
    height: 24px;
  }
  .contact-icon { width: 17px; height: 17px; flex: none; }
  /* Back */
  .card-back {
    left: 620px; top: 225px;
    background: linear-gradient(150deg, var(--card-grey-light) 0%, #737378 50%, var(--card-grey-dark) 100%);
    display: flex; flex-direction: column; align-items: center; justify-content: center;
  }
  .card-back .brand-name {
    color: #ffffff;
    font-size: 76px;
  }
  .card-back .tagline {
    color: var(--text-soft);
    font-size: 18px;
    margin-top: 12px;
    letter-spacing: 0.4px;
  }
</style>
</head>
<body>

<section class="card card-front" aria-label="Business card front">
  <div class="front-brand">
    <div class="brand-name">bluvoria</div>
    <div class="tagline">Your business and accounting partner</div>
  </div>

  <div class="person">
    <div class="person-name">Marcy Elwind</div>
  </div>
  <div class="divider"></div>
  <div class="person-role">(Principal)<br>Accountant, Tax Agent</div>
  <div class="address">Carrowby NSW<br>Australia</div>

  <ul class="contact-list">
    <li class="contact-item">
      <svg class="contact-icon" viewBox="0 0 17 17" aria-hidden="true">
        <rect width="17" height="17" rx="2" fill="#21a9dc"/>
        <path d="M5 4.5c.6-.4 1.2-.3 1.5.3l.7 1.4c.2.5 0 .9-.4 1.2l-.4.3c.5 1.2 1.4 2.1 2.6 2.6l.3-.4c.3-.4.8-.6 1.2-.4l1.4.7c.6.3.7.9.3 1.5-.6.8-1.5 1.1-2.5.7C7.4 11.4 5.6 9.6 4.6 7.3c-.4-1 -.1-2 .4-2.8z" fill="#fff"/>
      </svg>
      <span>0417 683 912</span>
    </li>
    <li class="contact-item">
      <svg class="contact-icon" viewBox="0 0 17 17" aria-hidden="true">
        <rect width="17" height="17" rx="2" fill="#21a9dc"/>
        <rect x="3.5" y="5" width="10" height="7" fill="none" stroke="#fff" stroke-width="1.2"/>
        <path d="M3.5 5l5 4 5-4" fill="none" stroke="#fff" stroke-width="1.2"/>
      </svg>
      <span>Marcy.Elwind@bluvoria.com.au</span>
    </li>
    <li class="contact-item">
      <svg class="contact-icon" viewBox="0 0 17 17" aria-hidden="true">
        <rect width="17" height="17" rx="2" fill="#21a9dc"/>
        <circle cx="8.5" cy="8.5" r="5" fill="none" stroke="#fff" stroke-width="1.1"/>
        <ellipse cx="8.5" cy="8.5" rx="2.2" ry="5" fill="none" stroke="#fff" stroke-width="1"/>
        <path d="M3.5 8.5h10M4.3 6h8.4M4.3 11h8.4" stroke="#fff" stroke-width="0.9"/>
      </svg>
      <span>www.bluvoria.com.au</span>
    </li>
  </ul>
</section>

<section class="card card-back" aria-label="Business card back">
  <div class="brand-name">bluvoria</div>
  <div class="tagline">Your business and accounting partner</div>
</section>

</body>
</html>
```